Business card for law firm

Need business card for new law firm. Think confident, authoritative, conservative, but not stuffy or old-fashioned.

Contact Information for Business Card

Content for card - logo (uploaded), plus the following:

Paul Whitcombe (larger font)
Managing Partner (larger font, but not as large as name)
Level 9, 7 Ferris Lane
Sydney NSW 2000
Main Tel 02 9364 2710
Direct Tel 02 8472 3159
Email paul@qvlegal.com.au
www.qvlegal.com.au

Letterhead design should include logo plus:
Level 9, 7 Ferris Lane
Sydney NSW 2000
Tel 02 8472 3159
www.qvlegal.com.au

```html
<!DOCTYPE html>
<html lang="en">
<head>
<meta charset="utf-8">
<title>Quayvale Legal – Business Card</title>
<link href="https://fonts.googleapis.com/css2?family=Open+Sans:wght@400;600;700&display=swap" rel="stylesheet">
<style>
  :root {
    --backdrop: #3b322d;
    --card: #1f2022;
    --ink: #f2f2f2;
    --ink-soft: #c9c9c9;
    --rule: #e6e6e6;
  }
  * { margin: 0; padding: 0; box-sizing: border-box; }
  html, body {
    width: 1200px; height: 864px; overflow: hidden;
    background: var(--backdrop);
    font-family: "Open Sans", Arial, sans-serif;
    color: var(--ink);
  }
  .canvas { position: relative; width: 1200px; height: 864px; }
  .card {
    position: absolute;
    width: 520px; height: 316px;
    background: var(--card);
    border-radius: 3px;
    box-shadow: 0 12px 30px rgba(0,0,0,.45);
  }
  /* Back of card */
  .card--back { left: 60px; top: 80px; }
  .back-brand {
    position: absolute; left: 0; right: 0; top: 100px;
    display: flex; align-items: center; justify-content: center; gap: 14px;
  }
  .brand-mark { width: 22px; height: 22px; background: var(--ink-soft); }
  .back-brand .brand-name {
    font-weight: 600; font-size: 30px; letter-spacing: 4px;
    text-transform: uppercase; color: var(--ink-soft);
  }
  .back-web {
    position: absolute; left: 0; right: 0; top: 218px;
    text-align: center; font-size: 15px; letter-spacing: 7px; color: var(--ink-soft);
  }
  /* Front of card */
  .card--front { left: 620px; top: 460px; }
  .front-brand {
    position: absolute; right: 30px; top: 52px;
    display: flex; align-items: center; gap: 10px;
  }
  .front-brand .brand-mark { width: 16px; height: 16px; background: var(--ink); }
  .front-brand .brand-name {
    font-weight: 600; font-size: 24px; letter-spacing: 3px;
    text-transform: uppercase; color: var(--ink);
  }
  .holder { position: absolute; left: 30px; top: 52px; }
  .holder-name { font-weight: 700; font-size: 18px; text-transform: uppercase; line-height: 1.1; }
  .holder-role { font-weight: 700; font-size: 13px; text-transform: uppercase; line-height: 1.3; }
  .contacts { list-style: none; margin-top: 8px; }
  .contacts li { display: flex; align-items: center; gap: 10px; font-size: 13px; line-height: 19px; }
  .contacts svg { width: 12px; height: 12px; flex: none; }
  .divider {
    position: absolute; left: 30px; right: 30px; top: 172px;
    height: 1.5px; background: var(--rule);
  }
  .address {
    position: absolute; right: 30px; top: 196px;
    text-align: right; font-size: 14px; line-height: 21px;
  }
</style>
</head>
<body>
<main class="canvas">
  <section class="card card--back" aria-label="Card back">
    <div class="back-brand">
      <span class="brand-mark"></span>
      <span class="brand-name">Quayvale Legal</span>
    </div>
    <p class="back-web">www.qvlegal.com.au</p>
  </section>

  <section class="card card--front" aria-label="Card front">
    <div class="holder">
      <h1 class="holder-name">Paul Whitcombe</h1>
      <p class="holder-role">Managing Partner</p>
      <ul class="contacts">
        <li>
          <svg viewBox="0 0 12 12" fill="none" stroke="currentColor" stroke-width="1.2"><path d="M2 4c0-1.5 1.5-2 4-2s4 .5 4 2l-1.5 1L7 4H5L3.5 5z"/><rect x="3" y="6" width="6" height="4" rx="1"/></svg>
          02 9364 2710
        </li>
        <li>
          <svg viewBox="0 0 12 12" fill="none" stroke="currentColor" stroke-width="1.2"><rect x="3.5" y="1" width="5" height="10" rx="1"/><line x1="5.5" y1="9.5" x2="6.5" y2="9.5"/></svg>
          02 8472 3159
        </li>
        <li>
          <svg viewBox="0 0 12 12" fill="currentColor"><path d="M1 3h10v6H1z"/><path d="M1 3l5 3.5L11 3" stroke="#1f2022" stroke-width="1" fill="none"/></svg>
          paul@qvlegal.com.au
        </li>
      </ul>
    </div>
    <div class="front-brand">
      <span class="brand-mark"></span>
      <span class="brand-name">Quayvale Legal</span>
    </div>
    <div class="divider"></div>
    <address class="address" style="font-style:normal">
      Level 9, 7 Ferris Lane<br>
      Sydney NSW 2000<br>
      www.qvlegal.com.au
    </address>
  </section>
</main>
</body>
</html>
```